Food and Beverage Business Cards

We need business cards with logo designs for a consultant in the food and beverage industry. We specialize in helping restaurants fix operational and management problems.
Specific areas of expertise include:
-Steps of service
-Staff management tools
-Standard operating procedures
-Profit and loss management
-Inventory
-Point of sales
-Bar Menu
-Mystery shopper service
-Handling and managing suppliers

Target Market(s)

Restaurant and bar owners and managers

Industry/Entity Type

Business

Contact Information for Business Card

Mathieu Girardot
Q&T Consulting
phone: 15027390614
mathqt@sampleinbox.com

Font styles to use
Other font styles liked:
• Check out the screen shot font idea

Colors

Designer to choose colors to be used in the design.

Requirements
Must have
• Must include QR code (See attachment)
• Logo should reflect our specific focus on the drinks side of the industry.
• Areas of Expertise:
• -Service Steps
• -Staff management tools
• -S.O.P
• -P&L Management
• -Inventory
• -P.O.S
• -Bar Menu
• -Mystery Shopper Service
• -Handling and Managing Suppliers

```html
<!DOCTYPE html>
<html lang="en">
<head>
<meta charset="utf-8">
<title>Q&amp;T Savannah Business Cards</title>
<link rel="stylesheet" href="https://fonts.googleapis.com/css2?family=Open+Sans:wght@400;600;700&display=swap">
<style>
  :root {
    --backdrop: #3a3a3c;
    --card-black: #0e0e0e;
    --card-white: #f4f4f4;
    --ink-white: #ffffff;
    --ink-soft: #e2e2e2;
    --ink-black: #141414;
    --wave-edge: #9a9a9a;
    --badge-green: #4f8a3c;
    --badge-grey: #d8d8d8;
  }
  * { margin: 0; padding: 0; box-sizing: border-box; }
  html, body { width: 1200px; height: 960px; overflow: hidden; }
  body {
    background: var(--backdrop);
    font-family: "Open Sans", Arial, sans-serif;
    display: flex;
    flex-direction: column;
    align-items: center;
    justify-content: center;
    gap: 56px;
  }
  .card {
    position: relative;
    width: 660px;
    height: 377px;
    border-radius: 4px;
    overflow: hidden;
    box-shadow: 0 10px 30px rgba(0,0,0,0.45);
  }

  /* Back of card */
  .card-back { background: var(--card-black); color: var(--ink-white); }
  .card-back .badges {
    position: absolute; top: 22px; right: 24px;
    display: flex; gap: 12px;
  }
  .badge { width: 38px; height: 38px; border-radius: 50%; }
  .badge-green { background: var(--badge-green); }
  .badge-grey { background: var(--badge-grey); border: 3px solid #777; }
  .badge-white { background: var(--ink-white); border: 3px solid #555; }
  .card-back .wordmark {
    position: absolute; top: 78px; left: 0; right: 0;
    text-align: center; color: var(--ink-white);
  }
  .wordmark { font-weight: 600; line-height: 1; }
  .wordmark .mark-main { display: block; font-size: 78px; letter-spacing: 2px; }
  .wordmark .mark-place { display: block; font-size: 20px; letter-spacing: 6px; margin-top: 4px; }
  .expertise {
    position: absolute; top: 232px; left: 0; right: 0;
    text-align: center;
  }
  .expertise-title { font-size: 19px; font-weight: 700; margin-bottom: 6px; }
  .expertise-list { font-size: 15px; line-height: 1.45; color: var(--ink-soft); }

  /* Front of card */
  .card-front { background: var(--card-white); }
  .card-front .wave { position: absolute; inset: 0; width: 100%; height: 100%; }
  .card-front .wordmark {
    position: absolute; top: 78px; right: 56px;
    text-align: center; color: var(--ink-black);
  }
  .contact {
    position: absolute; left: 30px; top: 186px;
    color: var(--ink-white);
  }
  .contact-name { font-size: 20px; font-weight: 700; text-transform: uppercase; }
  .contact-company { font-size: 15px; text-transform: uppercase; margin-bottom: 8px; }
  .contact-line { display: flex; align-items: center; gap: 8px; font-size: 15px; line-height: 1.6; }
  .contact-line svg { width: 13px; height: 13px; fill: var(--ink-white); flex: none; }
</style>
</head>
<body>

  <section class="card card-back">
    <div class="badges">
      <div class="badge badge-green"></div>
      <div class="badge badge-grey"></div>
      <div class="badge badge-white"></div>
    </div>
    <div class="wordmark">
      <span class="mark-main">Q&amp;T</span>
      <span class="mark-place">savannah</span>
    </div>
    <div class="expertise">
      <p class="expertise-title">Areas of Expertise</p>
      <p class="expertise-list">
        Service Steps | Staff management tools | S.O.P | P&amp;L Management<br>
        Inventory | P.O.S | Bar Menu | Mystery Shopper Service<br>
        Handling and Managing Suppliers
      </p>
    </div>
  </section>

  <section class="card card-front">
    <svg class="wave" viewBox="0 0 660 377" preserveAspectRatio="none" aria-hidden="true">
      <path d="M0 150 C 120 95, 250 110, 340 200 S 500 370, 580 377 L 0 377 Z" fill="#8c8c8c"/>
      <path d="M0 160 C 120 108, 248 122, 332 210 S 490 377, 560 377 L 0 377 Z" fill="#0e0e0e"/>
    </svg>
    <div class="wordmark">
      <span class="mark-main">Q&amp;T</span>
      <span class="mark-place">savannah</span>
    </div>
    <div class="contact">
      <p class="contact-name">Mathieu Girardot</p>
      <p class="contact-company">Q&amp;T Consulting</p>
      <p class="contact-line">
        <svg viewBox="0 0 16 16"><path d="M3 1h3l1.5 4-2 1.2a9 9 0 0 0 4.3 4.3L11 8.5l4 1.5v3a2 2 0 0 1-2 2A13 13 0 0 1 1 3a2 2 0 0 1 2-2z"/></svg>
        15027390614
      </p>
      <p class="contact-line">
        <svg viewBox="0 0 16 16"><path d="M1 3h14v10H1z" /><path d="M1 3l7 6 7-6" fill="none" stroke="#0e0e0e" stroke-width="1.5"/></svg>
        mathqt@sampleinbox.com
      </p>
    </div>
  </section>

</body>
</html>
```